The book will contain the papers written by presenters at the Fresh Horizons in Beyond Contact conference held by the Institute for Luminous and Awareness Research. There will be something like 19 chapters, each about a different method people are using today to have afterlife communication with loved ones on the other side. The cover must be upbeat, inspiring, full of joy and life. Nothing with ghosts or cemeteries or skeletons or hauntings. It's about family members communicating with loved ones who are alive and well, just living on a different plane. Any image of uniting, love, and togetherness is a plus. The author name is Institute for Luminous and Awareness Research.

Industry/Entity Type

Communication

```html
<!DOCTYPE html>
<html lang="en">
<head>
<meta charset="utf-8">
<title>Fresh Horizons in Beyond Contact — Book Cover</title>
<link rel="stylesheet" href="https://fonts.googleapis.com/css2?family=Cinzel:wght@400;600;700&display=swap">
<style>
  :root {
    --backdrop: #2f7fc6;
    --title-yellow: #f6ea1e;
    --title-glow: rgba(255, 214, 90, 0.75);
    --sky-light: #f3dfb4;
    --sky-warm: #c89a5c;
    --sea-mid: #6e5238;
    --shore-dark: #2e2218;
    --caption: #f4ead6;
    --badge-blue: #2f5fa8;
  }
  * { margin: 0; padding: 0; box-sizing: border-box; }
  html, body {
    width: 1024px;
    height: 1200px;
    overflow: hidden;
    background: var(--backdrop);
  }
  .canvas {
    position: relative;
    width: 1024px;
    height: 1200px;
  }
  .book-cover {
    position: absolute;
    left: 122px;
    top: 75px;
    width: 780px;
    height: 1050px;
    overflow: hidden;
    font-family: "Cinzel", "Trajan Pro", serif;
  }
  .cover-photo {
    position: absolute;
    inset: 0;
    background:
      radial-gradient(ellipse 38% 22% at 50% 9%, rgba(255, 246, 215, 0.95), rgba(255, 230, 170, 0) 100%),
      radial-gradient(ellipse 70% 30% at 55% 25%, rgba(236, 200, 140, 0.7), rgba(236, 200, 140, 0) 100%),
      linear-gradient(180deg,
        #8a6a48 0%,
        var(--sky-warm) 14%,
        var(--sky-light) 26%,
        #b88e5c 40%,
        #8d6a48 50%,
        var(--sea-mid) 60%,
        #4a3726 75%,
        var(--shore-dark) 100%);
  }
  .cover-title {
    position: absolute;
    left: 22px;
    top: 418px;
    color: var(--title-yellow);
    font-weight: 600;
    font-size: 52px;
    line-height: 70px;
    letter-spacing: 3px;
    text-shadow: 0 0 12px var(--title-glow), 0 0 3px rgba(120, 70, 0, 0.6);
  }
  .cover-title .line { display: block; white-space: nowrap; }
  .cover-title .cap { font-size: 66px; }
  .cover-title .small { letter-spacing: 7px; }
  .cover-subtitle {
    position: absolute;
    left: 40px;
    right: 40px;
    top: 738px;
    color: var(--caption);
    font-size: 12.5px;
    line-height: 17px;
    letter-spacing: 1.2px;
    text-align: center;
    text-transform: uppercase;
  }
  .publisher-mark {
    position: absolute;
    left: 50%;
    top: 948px;
    transform: translateX(-50%);
    display: flex;
    align-items: center;
    gap: 10px;
  }
  .publisher-mark .dot {
    width: 22px;
    height: 22px;
    border-radius: 50%;
    background: var(--badge-blue);
  }
  .publisher-mark .name {
    color: var(--caption);
    font-size: 30px;
    font-weight: 600;
    letter-spacing: 2px;
  }
  .author-line {
    position: absolute;
    left: 0;
    right: 0;
    bottom: 12px;
    color: var(--caption);
    font-size: 13.5px;
    letter-spacing: 0.8px;
    text-align: center;
    text-transform: uppercase;
  }
</style>
</head>
<body>
<div class="canvas">
  <section class="book-cover">
    <div class="cover-photo" role="img" aria-label="Sepia sunset photograph of a tall lighthouse on a shoreline, its lamp glowing against a bright cloudy sky, with seabirds flying and a sandy path leading to the sea"></div>

    <h1 class="cover-title">
      <span class="line"><span class="cap">F</span>resh</span>
      <span class="line"><span class="cap">H</span>orizons</span>
      <span class="line"><span class="cap">I</span>n <span class="small">beyond</span></span>
      <span class="line"><span class="cap">C</span>ontact</span>
    </h1>

    <p class="cover-subtitle">19 chapters, each about a different method people are using today to have afterlife communication with loved ones on the other side</p>

    <div class="publisher-mark">
      <span class="dot"></span>
      <span class="name">ILAR</span>
    </div>

    <p class="author-line">Institute for Luminous and Awareness Research</p>
  </section>
</div>
</body>
</html>
```